Velmor Spire Nine Flash website

we need a website to cater to 2 aspect of the business. We have Velmor spire residence and velmor spire office. For the office, we will get their inquire and arrange a face to face meetup to show them the office area for rent. For the residence side, it will need to be like staylane or roomvio.com. we want to allow them to book online for the date they need. We have a total of 10 different room configurations starting at $70 per night and up depending on the size of the room. example of the design is https://brisquelodge.com/

Target Market(s)

the website should have detail information on the layout, designs, and luxury of the building.

Industry/Entity Type

office and service appartment rental/lease

Coding

Coded - Design and coding required

Number of Pages Required

5+ page

Requirements
Must have
• a luxury perspective
Nice to have
• example https://brisquelodge.com/

```html
<!DOCTYPE html>
<html lang="en">
<head>
<meta charset="UTF-8">
<title>Velmor Spire Nine</title>
<link rel="stylesheet" href="https://fonts.googleapis.com/css2?family=Montserrat:wght@600;700;800&display=swap">
<style>
  :root {
    --gold: #d3992a;
    --white: #ffffff;
    --ink: #111111;
    --room-dark: #1c1c1e;
    --room-mid: #3a3a3d;
    --room-light: #55555a;
    --night-blue: #2a3550;
  }
  * { margin: 0; padding: 0; box-sizing: border-box; }
  html, body {
    width: 1200px;
    height: 729px;
    overflow: hidden;
    background: var(--room-dark);
  }
  .hero {
    position: relative;
    width: 1200px;
    height: 729px;
    overflow: hidden;
    font-family: "Montserrat", Arial, sans-serif;
  }
  .hero__backdrop {
    position: absolute;
    inset: 0;
    background:
      radial-gradient(ellipse 220px 260px at 760px 250px, rgba(42,53,80,0.85), transparent 70%),
      radial-gradient(ellipse 520px 260px at 520px 520px, rgba(95,95,100,0.55), transparent 75%),
      linear-gradient(180deg, var(--room-mid) 0%, var(--room-dark) 45%, var(--room-mid) 80%, var(--room-light) 100%);
  }
  .hero__shade {
    position: absolute;
    inset: 0;
    background: rgba(0,0,0,0.35);
  }
  .brand {
    position: absolute;
    top: 56px;
    left: 0;
    width: 100%;
    display: flex;
    flex-direction: column;
    align-items: center;
    gap: 34px;
  }
  .brand__square {
    width: 62px;
    height: 62px;
    border: 2px solid var(--gold);
  }
  .brand__name {
    color: var(--gold);
    font-weight: 600;
    font-size: 30px;
    letter-spacing: 1px;
    line-height: 1;
  }
  .headline {
    position: absolute;
    top: 272px;
    left: 0;
    width: 100%;
    text-align: center;
    color: var(--white);
    font-weight: 800;
    font-size: 64px;
    line-height: 77px;
    letter-spacing: 0.5px;
    text-transform: uppercase;
  }
  .choices {
    position: absolute;
    top: 459px;
    left: 0;
    width: 100%;
    display: flex;
    justify-content: center;
    gap: 35px;
  }
  .choice {
    width: 265px;
    height: 65px;
    border-radius: 33px;
    display: flex;
    align-items: center;
    justify-content: center;
    color: var(--ink);
    font-weight: 700;
    font-size: 15px;
    text-transform: uppercase;
    text-decoration: none;
  }
  .choice--residence { background: var(--gold); }
  .choice--office { background: var(--white); }
</style>
</head>
<body>
  <main class="hero">
    <div class="hero__backdrop" role="img" aria-label="Dimly lit luxury hotel bedroom with upholstered bed, bench, armchair and night city view through tall windows"></div>
    <div class="hero__shade"></div>

    <div class="brand">
      <div class="brand__square"></div>
      <div class="brand__name">Velmor Spire Nine</div>
    </div>

    <h1 class="headline">Welcome to<br>Velmor Spire Nine</h1>

    <nav class="choices">
      <a class="choice choice--residence" href="#residence">Velmor Spire Residence</a>
      <a class="choice choice--office" href="#office">Tower Office.</a>
    </nav>
  </main>
</body>
</html>
```